Letterhead for Business Law Firm

We need a letter head for our firm based on the design we have settled on and it is attached. Our clients are small and large businesses around the world, and our letterhead is used typically for formal legal purposes such as demand letters (accusing the recipient of doing bad things) or responding to demand letters. It may also be sent to regulators and other government agencies. So this needs to be tasteful, but a little edgy as well - we try to convey that we are a firm that is different - businesses and investors come to us for creative, quick advice, typically in high stress circumstances, and for our ability to work through high conflict situations, and rapid paced engagements.

Target Market(s)

Lawyers, business executives, investors, government regulators who may receive letters from this firm on behalf of its clients.

Industry/Entity Type

Business

Requirements
Must have
• The design and the firm's contact information:
• Thornwell Law Firm, P.C.
• 1876 NE 57th Ave
• Portland, OR 97213
• phone: 971 555 0147
• fax: 971 555 0182
• in what placement and how depicted (e.g. a phone icon instead of the word "phone") I leave to your creative ideas.
Nice to have
• design and information can be placed at the top, bottom and/or sides of the letter, and the design should be for a standard letter size paper - and can have a separate design for the second page.

```html
<!DOCTYPE html>
<html lang="en">
<head>
<meta charset="utf-8">
<title>Thornwell Law Firm, P.C. — Letterhead</title>
<link rel="stylesheet" href="https://fonts.googleapis.com/css2?family=Josefin+Sans:wght@300&family=Source+Sans+3:wght@400&display=swap">
<style>
  :root {
    --paper-top: #ffffff;
    --paper-bottom: #efefef;
    --ink: #3a3a3a;
    --accent: #2f6b73;
    --mark-dark: #1c1517;
    --band-light: #e6e6e6;
    --band-dark: #d9d9d9;
  }
  * { margin: 0; padding: 0; box-sizing: border-box; }
  html, body {
    width: 923px;
    height: 1200px;
    overflow: hidden;
    background: #ffffff;
  }
  .letterhead {
    position: relative;
    width: 923px;
    height: 1200px;
    background: linear-gradient(160deg, var(--paper-top) 40%, var(--paper-bottom) 100%);
    font-family: "Source Sans 3", "Myriad Pro", sans-serif;
    color: var(--ink);
  }
  .firm-mark {
    position: absolute;
    top: 52px;
    left: 0;
    width: 100%;
    display: flex;
    justify-content: center;
    align-items: center;
    gap: 14px;
  }
  .firm-mark__square {
    width: 40px;
    height: 54px;
    background: var(--mark-dark);
  }
  .firm-mark__name {
    font-family: "Josefin Sans", sans-serif;
    font-weight: 300;
    font-size: 44px;
    letter-spacing: 10px;
    color: var(--mark-dark);
    line-height: 1;
    padding-top: 8px;
  }
  .footer-band {
    position: absolute;
    left: 0;
    bottom: 0;
    width: 100%;
    height: 140px;
    background: linear-gradient(90deg, var(--band-light), var(--band-dark) 50%, var(--band-light));
  }
  .contact {
    position: absolute;
    left: 0;
    bottom: 28px;
    width: 100%;
    text-align: center;
    font-size: 18px;
    line-height: 36px;
  }
  .contact__row {
    display: flex;
    justify-content: center;
    align-items: center;
    gap: 12px;
  }
  .contact__item {
    display: inline-flex;
    align-items: center;
    gap: 6px;
  }
  .contact__icon {
    width: 16px;
    height: 16px;
    fill: none;
    stroke: var(--accent);
    stroke-width: 1.6;
  }
</style>
</head>
<body>
  <main class="letterhead">
    <header class="firm-mark">
      <span class="firm-mark__square"></span>
      <span class="firm-mark__name">THORNWELL</span>
    </header>

    <div class="footer-band" role="img" aria-label="Faint storm-sky band behind the contact details"></div>

    <footer class="contact">
      <div class="contact__row">
        <span class="contact__item">
          <svg class="contact__icon" viewBox="0 0 16 16" aria-label="Phone"><circle cx="8" cy="8" r="7"/><path d="M6 4.5 L5 6 C5.5 8.5 7.5 10.5 10 11 L11.5 10"/></svg>
          971 555 0147
        </span>
        <span class="contact__item">
          <svg class="contact__icon" viewBox="0 0 16 16" aria-label="Fax"><rect x="4" y="1.5" width="8" height="13" rx="1"/><path d="M5.5 4h5v3h-5z M6 9.5h1 M9 9.5h1 M6 12h1 M9 12h1"/></svg>
          971 555 0182
        </span>
        <span class="contact__item">
          <svg class="contact__icon" viewBox="0 0 16 16" aria-label="Email"><path d="M1.5 6.5 L8 2 L14.5 6.5 V13.5 H1.5 Z M1.5 6.5 L8 10.5 L14.5 6.5"/></svg>
          info@thornwelllaw.com
        </span>
        <span class="contact__item">
          <svg class="contact__icon" viewBox="0 0 16 16" aria-label="Website"><circle cx="8" cy="8" r="6.5"/><ellipse cx="8" cy="8" rx="3" ry="6.5"/><path d="M1.5 8h13 M2.5 5h11 M2.5 11h11"/></svg>
          www.thornwelllaw.com
        </span>
      </div>
      <div class="contact__row">
        <span class="contact__item">
          <svg class="contact__icon" viewBox="0 0 16 16" aria-label="Address"><path d="M1.5 14.5h13 M2.5 14.5V7L8 3l5.5 4v7.5 M5 9h6 M5 11.5h6"/></svg>
          1876 NE 57th Ave, Portland, OR 97213
        </span>
      </div>
    </footer>
  </main>
</body>
</html>
```